Korval Advise Business Cards

We need a business card design for Korval Advise (Logo Attached), a management consultancy specialized in brand & business building.

Design should be clean, smart and a touch of innnovation without being gimmicky.

The details on the card should be:
Name: Tomas Velduren
Title: Managing Director
Address: 42 Marlowe Pier, Tarn Vessel Tower, Singapore 073926
Tel: +6285927461082
email: tv@korvaladvise.example
website: korvaladvise.example

For further background on corporate identity, please check www.korvaladvise.example
Updates

Dear all,

Many thanks for the submissions so far! I gave feedback to those designs that I prefer at this stage.

Overall I see that my preference goes into the direction that 'less is more' and 'simple is beautiful'

Please create uniqueness and standout by the simplicity and attraction of the overall concept and design.

Many thanks and please shout incase of questions!

Tomas

Industry/Entity Type

Business

```html
<!DOCTYPE html>
<html lang="en">
<head>
<meta charset="utf-8">
<title>Korval Advise Business Cards</title>
<link rel="stylesheet" href="https://fonts.googleapis.com/css2?family=Open+Sans:wght@400;600;700&display=swap">
<style>
  :root {
    --ink: #4a4a4a;
    --orange: #ff6600;
    --paper: #ffffff;
    --backdrop: #ece8e3;
    --card-edge: #3a3a3a;
    --text: #333333;
  }
  * { box-sizing: border-box; margin: 0; padding: 0; }
  html, body {
    width: 1200px; height: 1105px; overflow: hidden;
    background: var(--backdrop);
    font-family: "Open Sans", Arial, sans-serif;
  }
  .canvas { position: relative; width: 1200px; height: 1105px; }

  .card { position: absolute; width: 857px; height: 489px; }
  .card-front { left: 36px; top: 39px; background: var(--paper); border: 1.5px solid var(--card-edge); }
  .card-back { left: 296px; top: 564px; background: var(--orange); }

  .wordmark {
    position: absolute; left: 0; right: 0; text-align: center;
    font-weight: 600; line-height: 1; white-space: nowrap;
  }
  .card-front .wordmark { top: 74px; font-size: 66px; color: var(--ink); }
  .card-back .wordmark { top: 170px; font-size: 82px; color: var(--paper); }

  .rule { position: absolute; top: 273px; height: 4px; background: var(--ink); }
  .rule-left { left: 0; width: 297px; }
  .rule-right { left: 558px; right: 0; }

  .holder { position: absolute; left: 0; right: 0; text-align: center; color: var(--ink); }
  .holder-name { top: 248px; font-size: 26px; font-weight: 700; }
  .holder-title { top: 284px; font-size: 21px; color: var(--orange); }

  .contact {
    position: absolute; left: 0; right: 0;
    font-size: 20px; color: var(--text); display: flex; justify-content: center;
    align-items: center; gap: 8px; white-space: nowrap;
  }
  .contact svg { width: 18px; height: 18px; fill: none; stroke: var(--text); stroke-width: 1.8; }
  .contact-phone { top: 340px; }
  .contact-web { top: 373px; }
  .contact-web .sep { width: 8px; }
  .contact-address { top: 425px; }

  .back-url {
    position: absolute; left: 0; right: 0; top: 342px; text-align: center;
    color: var(--paper); font-size: 20px; letter-spacing: 0.24em; white-space: nowrap;
  }
</style>
</head>
<body>
<main class="canvas">
  <section class="card card-front" aria-label="Business card front">
    <div class="wordmark">Korval Advise</div>
    <div class="rule rule-left"></div>
    <div class="rule rule-right"></div>
    <div class="holder holder-name">Tomas Velduren</div>
    <div class="holder holder-title">Managing Director</div>
    <div class="contact contact-phone">
      <svg viewBox="0 0 24 24" aria-hidden="true"><path d="M5 3h4l2 5-2.5 1.5a11 11 0 0 0 6 6L16 13l5 2v4a2 2 0 0 1-2 2A16 16 0 0 1 3 5a2 2 0 0 1 2-2z"/></svg>
      <span>+6285927461082</span>
    </div>
    <div class="contact contact-web">
      <svg viewBox="0 0 24 24" aria-hidden="true"><rect x="3" y="6" width="18" height="13" rx="1"/><path d="M3 7l9 6 9-6"/></svg>
      <span>tv@korvaladvise.example</span>
      <span class="sep"></span>
      <svg viewBox="0 0 24 24" aria-hidden="true"><circle cx="12" cy="12" r="9"/><path d="M3 12h18M12 3c3 3 3 15 0 18M12 3c-3 3-3 15 0 18"/></svg>
      <span>www.korvaladvise.example</span>
    </div>
    <div class="contact contact-address">42 Marlowe Pier, Tarn Vessel Tower, Singapore 073926</div>
  </section>

  <section class="card card-back" aria-label="Business card back">
    <div class="wordmark">Korval Advise</div>
    <div class="back-url">www.korvaladvise.example</div>
  </section>
</main>
</body>
</html>
```